ORV Web Design Project

I'm looking for a small, friendly,functional, information based website. If you go through the attachments, you would know the nature of the business.
Updates

Hi,

I have uploaded a picture of the CEO, Mr. Delvan Kroth PLMAT member. Please feel free to use it whereever appropriate.

Thanks!

Hello, I have uploaded some references. I like the colours used on the bar and would w

Example of a we page . I like this layout for the inside pages.

I am changing the tabs on my website to:

Home
About us
Services
Contact us

The services tab will have three sub pages:

Immigration
Education
AccommodationAccommodation

Target Market(s)

Young international students willing to come to Canada to study, young international students willing to immigrate to Canada, parents of the students

Industry/Entity Type

Business

Requirements
Must have
• ORV HOME
ABOUT US
CONTACT
SERVICES
TAG LINE

The website should look n feel trendy, smart, current, factual, trustworthy etc....
Nice to have
• I am looking for a bold, attractive, eye catchy home page with less text! Something that makes a statement....
Should not have
• No Clip art, flash animation, no bells n whistles please

```html
<!DOCTYPE html>
<html lang="en">
<head>
<meta charset="utf-8">
<title>ORV — Orvale Business Group</title>
<link href="https://fonts.googleapis.com/css2?family=Oswald:wght@300;400&family=Roboto:wght@400;700&family=Dancing+Script:wght@500&display=swap" rel="stylesheet">
<style>
:root{
  --red:#e31b23;
  --ink:#1f1f1f;
  --grey:#8a8a8a;
  --map:#ececec;
  --panel-dark:#4b4b4b;
  --panel-light:#f3f3f3;
  --header-dark:#3a3a3a;
  --white:#ffffff;
}
*{box-sizing:border-box;margin:0;padding:0}
html,body{width:1200px;height:826px;overflow:hidden;background:var(--white)}
body{position:relative;font-family:"Roboto",Arial,sans-serif;color:var(--ink)}
.abs{position:absolute}
.backdrop-map{left:120px;top:10px;width:930px;height:740px;border-radius:45% 40% 35% 50%;
  background:radial-gradient(ellipse at 50% 45%,#efefef 0%,#f5f5f5 55%,rgba(255,255,255,0) 75%)}
.brand{left:176px;top:40px}
.brand-mark{display:flex;align-items:center;gap:10px}
.brand-name{font-family:"Roboto",sans-serif;font-weight:700;font-size:46px;line-height:1;color:var(--ink);letter-spacing:1px}
.brand-square{width:34px;height:34px;background:var(--red)}
.brand-full{margin-top:8px;font-family:"Oswald",sans-serif;font-weight:400;font-size:25px;color:var(--grey);line-height:1}
.social-top{left:913px;top:49px;display:flex;gap:11px}
.social-top span,.social-contact span{display:block;width:21px;height:21px;background:var(--red)}
.social-contact span{background:var(--ink);width:21px;height:21px}
.nav{left:613px;top:96px;display:flex;align-items:center;font-family:"Oswald",sans-serif;font-weight:300;font-size:21px;letter-spacing:1.5px;color:var(--ink)}
.nav .sep{color:var(--red);margin:0 21px;font-size:17px}
.tagline{left:0;width:1200px;top:152px;text-align:center;font-family:"Dancing Script",cursive;font-size:40px;color:var(--ink)}
.hero{left:168px;top:222px;width:858px;height:388px}
.photo-group{left:0;top:0;width:515px;height:388px;background:linear-gradient(180deg,#b9c8d3 0%,#8c7c6a 45%,#5a4a44 100%)}
.photo-video{left:515px;top:0;width:343px;height:136px;background:linear-gradient(90deg,#6b5a55,#9aa7b8 60%,#4b6ea3)}
.play{left:822px;top:262px;width:0;height:0}
.photo-grad{left:515px;top:136px;width:171px;height:116px;background:linear-gradient(135deg,#e8e4e6,#b0375c 80%)}
.gov-list{left:686px;top:136px;width:172px;height:116px;background:var(--panel-dark);color:var(--white);font-size:11px;line-height:13.3px;padding:13px 9px;letter-spacing:.2px}
.partner{left:344px;top:252px;width:171px;height:136px;background:var(--white);display:flex;align-items:center;justify-content:center;gap:10px}
.partner-circle{width:56px;height:56px;border-radius:50%;background:#4d8fcf}
.partner-name{font-family:"Roboto",sans-serif;font-size:26px;color:#4a4a4a;letter-spacing:1px}
.news{left:515px;top:252px;width:343px;height:136px;background:var(--panel-light);padding:15px 14px 0 15px}
.news h2{font-size:10.5px;font-weight:700;line-height:15.5px;color:#111}
.news p{margin-top:8px;font-size:10.5px;line-height:13px;color:#333}
.newsletter{left:170px;top:668px;width:257px;height:125px}
.newsletter-body{position:absolute;left:9px;top:28px;width:239px;height:97px;background:var(--white);border:1px solid #d6d6d6;box-shadow:0 1px 3px rgba(0,0,0,.15)}
.newsletter-head{position:absolute;left:0;top:0;width:257px;height:33px;background:linear-gradient(180deg,#555,var(--header-dark));color:var(--white);font-family:"Oswald",sans-serif;font-size:20px;line-height:33px;padding-left:23px}
.newsletter label{position:absolute;left:23px;top:48px;font-size:11px;color:#333}
.newsletter .field{position:absolute;left:23px;top:64px;width:198px;height:30px;border:1px solid #cfcfcf;background:var(--white)}
.newsletter .submit{position:absolute;left:161px;top:97px;width:61px;height:18px;background:linear-gradient(180deg,#eee,#cfcfcf);border:1px solid #bbb;font-family:"Oswald",sans-serif;font-size:12px;line-height:16px;text-align:center;color:#222}
.contact-title{left:474px;top:668px;font-family:"Oswald",sans-serif;font-size:21px;color:var(--ink)}
.social-contact{left:576px;top:672px;display:flex;gap:11px}
.contact-lines{left:474px;top:715px;font-size:10.5px;line-height:17px;color:var(--red)}
.contact-lines b{color:var(--ink)}
.footer-brand{left:908px;top:690px;display:flex;align-items:center;gap:8px}
.footer-brand .brand-name{font-size:40px}
.footer-brand .brand-square{width:30px;height:30px}
.copyright{left:765px;top:770px;font-size:11px;color:var(--ink)}
.base-band{left:0;top:804px;width:1200px;height:22px;background:var(--red)}
</style>
</head>
<body>
<div class="abs backdrop-map" role="img" aria-label="Faint map of Canada in the background"></div>

<header>
  <div class="abs brand">
    <div class="brand-mark"><span class="brand-name">ORV</span><span class="brand-square"></span></div>
    <div class="brand-full">Orvale Business Group</div>
  </div>
  <div class="abs social-top" aria-label="Social links"><span></span><span></span><span></span><span></span></div>
  <nav class="abs nav">
    <span>HOME</span><span class="sep">/</span>
    <span>ABOUT US</span><span class="sep">/</span>
    <span>CONTACT</span><span class="sep">/</span>
    <span>SERVICES</span>
  </nav>
  <div class="abs tagline">Taking you onwards......</div>
</header>

<main class="abs hero">
  <div class="abs photo-group" role="img" aria-label="Photo of four international students standing in a city square"></div>
  <div class="abs photo-video" role="img" aria-label="Video still of a group of smiling students"></div>
  <svg class="abs" style="left:659px;top:52px" width="58" height="58" viewBox="0 0 58 58" aria-label="Play video">
    <circle cx="29" cy="29" r="28" fill="#e31b23" opacity=".85"/>
    <polygon points="23,17 42,29 23,41" fill="#fff"/>
  </svg>
  <div class="abs photo-grad" role="img" aria-label="Photo of a graduate in cap and gown"></div>
  <div class="abs gov-list">
    Governor General<br>Prime Minister<br>Parliament<br>Senators<br>Members of Parliament<br>Supreme Court<br>Departments and Agencies
  </div>
  <div class="abs partner">
    <span class="partner-circle"></span><span class="partner-name">PLMAT</span>
  </div>
  <article class="abs news" style="left:515px">
    <h2>Government of Canada Committed to Research and Innovation:<br>Minister of State Hallberg Announces Funding to Top Academics</h2>
    <p>The Honourable Marcus Hallberg, Minister of State (Science and Technology), was at Northbrook University today to announce funding for new training initiatives in a variety of research areas, including genomics, climate change in the Arctic, clean combustion engines, and wireless technology.</p>
  </article>
</main>

<footer>
  <section class="abs newsletter">
    <div class="newsletter-body"></div>
    <div class="newsletter-head">SIGN UP FOR NEWSLETTER</div>
    <label>Email Address</label>
    <div class="field"></div>
    <div class="submit">SUBMIT</div>
  </section>

  <div class="abs contact-title">CONTACT</div>
  <div class="abs social-contact" aria-label="Social links"><span></span><span></span><span></span><span></span></div>
  <div class="abs contact-lines">
    <b>Address:</b> 418 Alder Street, Barrie, Ontario,<br>
    L4N 2K7 Canada<br>
    <b>Phone:</b> (705) 555 0142 (705) 555 0187<br>
    <b>Email:</b>info@orvalegroup.com
  </div>

  <div class="abs footer-brand"><span class="brand-name">ORV</span><span class="brand-square"></span></div>
  <div class="abs copyright">© 2013 Orvale Business Group. All Rights Reserved</div>
  <div class="abs base-band"></div>
</footer>
</body>
</html>
```